Veldmark Supplies Business Card

Professional business card that stand out to our potential customers. Front and back with clean modern design

Industry/Entity Type

Oil and gas

Contact Information for Business Card

Name, address, website , office phone and cell number

Requirements
Must have
• Editable files for each employee

```html
<!DOCTYPE html>
<html lang="en">
<head>
<meta charset="utf-8">
<title>Veldmark Supplies Business Card</title>
<link rel="stylesheet" href="https://fonts.googleapis.com/css2?family=Montserrat:wght@400;500;700;800&display=swap">
<style>
  :root{
    --stage:#2b2b2b;
    --card:#231f20;
    --red:#ed1c24;
    --cyan:#16aed0;
    --white:#ffffff;
  }
  *{box-sizing:border-box;margin:0;padding:0}
  html,body{width:1200px;height:988px;overflow:hidden;background:var(--stage)}
  body{position:relative;font-family:"Montserrat",sans-serif;color:var(--white)}
  .card{
    position:absolute;width:560px;height:320px;
    background:var(--card);border:5px solid var(--red);border-radius:38px;
    overflow:hidden;
  }
  .card--front{left:70px;top:90px}
  .card--back{left:570px;top:570px}

  .front-brand{
    position:absolute;inset:0;display:flex;align-items:center;justify-content:center;gap:14px;
  }
  .brand-square{width:22px;height:22px;background:var(--red)}
  .brand-name{font-weight:800;font-size:34px;letter-spacing:1px;color:var(--cyan);text-transform:uppercase}

  .back-brand{position:absolute;left:34px;top:78px;display:flex;align-items:center;gap:10px}
  .back-brand .brand-square{width:16px;height:16px}
  .back-brand .brand-name{font-size:22px}

  .holder{position:absolute;right:50px;top:42px;text-align:right}
  .holder-name{font-weight:800;font-size:30px;line-height:1}
  .holder-name .first{color:var(--red)}
  .holder-name .last{color:var(--cyan)}
  .holder-role{font-weight:500;font-size:13px;margin-top:6px;letter-spacing:.5px}
  .holder-tab{position:absolute;right:0;top:36px;width:26px;height:46px;background:var(--red);border-radius:6px 0 0 6px}

  .divider{position:absolute;left:34px;right:34px;top:150px;height:2px;background:var(--cyan)}

  .contacts{position:absolute;left:40px;top:176px;list-style:none}
  .contacts li{display:flex;align-items:center;gap:10px;font-size:14px;line-height:26px}
  .contacts svg{width:14px;height:14px;flex:none}

  .location{position:absolute;right:44px;top:188px;display:flex;align-items:center;gap:8px;font-size:14px}
  .location svg{width:12px;height:16px}
</style>
</head>
<body>

<section class="card card--front" aria-label="Card front">
  <div class="front-brand">
    <span class="brand-square"></span>
    <span class="brand-name">Veldmark Supplies</span>
  </div>
</section>

<section class="card card--back" aria-label="Card back">
  <div class="back-brand">
    <span class="brand-square"></span>
    <span class="brand-name">Veldmark Supplies</span>
  </div>

  <div class="holder">
    <p class="holder-name"><span class="first">Daniel</span> <span class="last">Okafor</span></p>
    <p class="holder-role">Manager</p>
  </div>
  <span class="holder-tab"></span>

  <div class="divider"></div>

  <ul class="contacts">
    <li><svg viewBox="0 0 24 24"><path fill="#ed1c24" d="M6.6 10.8a15 15 0 0 0 6.6 6.6l2.2-2.2a1 1 0 0 1 1-.25 11.4 11.4 0 0 0 3.6.57 1 1 0 0 1 1 1V20a1 1 0 0 1-1 1A17 17 0 0 1 3 4a1 1 0 0 1 1-1h3.5a1 1 0 0 1 1 1c0 1.25.2 2.45.57 3.57a1 1 0 0 1-.25 1z"/></svg>1-555-010-0199</li>
    <li><svg viewBox="0 0 24 24"><path fill="#ed1c24" d="M2 5h20v14H2z"/><path fill="none" stroke="#231f20" stroke-width="2" d="M2 5l10 8 10-8"/></svg>dokafor@veldmarkparts.vn</li>
    <li><svg viewBox="0 0 24 24"><g fill="none" stroke="#ed1c24" stroke-width="2"><circle cx="12" cy="12" r="9"/><path d="M3 12h18M12 3c3 3 3 15 0 18M12 3c-3 3-3 15 0 18"/></g></svg>www.veldmarkparts.vn</li>
    <li><svg viewBox="0 0 24 24"><g fill="none" stroke="#ed1c24" stroke-width="2"><circle cx="12" cy="12" r="9"/><path d="M3 12h18M12 3c3 3 3 15 0 18M12 3c-3 3-3 15 0 18"/></g></svg>www.veldmarkparts.com</li>
  </ul>

  <div class="location">
    <span>Lam Vien, Vietnam</span>
    <svg viewBox="0 0 12 16"><path fill="#ed1c24" d="M6 0a6 6 0 0 0-6 6c0 4.5 6 10 6 10s6-5.5 6-10a6 6 0 0 0-6-6zm0 8.3A2.3 2.3 0 1 1 6 3.7a2.3 2.3 0 0 1 0 4.6z"/></svg>
  </div>
</section>

</body>
</html>
```